App Design - Career Prep Pal

We require an App Design for our new App called 'Hiring Helper'. This app is essentially an assistant to help Users prepare for job interviews, to help them get hired. <br/><br/>Users who download the App can view common Questions and Answers, save their favourite responses and also view common Interview Tips. <br/><br/>The vision for our App is for Users who are preparing for an interview (1 week before, 1 day before, even 1 hour before), are able to download, view and educate themselves on common questions and responses, and then be confident to land the job. <br/><br/>Our team has developed wireframes to help highlight what each screen should do and include. Please see attached document, which also highlights key requirements for the experience. Feel free to add/remove/edit what you see on these wireframes. Our preference is that you use Adobe XD please.<br/><br/>In terms of design guidelines, we want the experience to be simple, intuitive and 'memorable' to help Users to remember the questions/responses when they are in the interview. <br/><br/>The final design should communicate 'neat and clean professionalism'; we like the design of: jobvista net au<br/><br/>Thank you for reading! Good luck !

Target Market(s)

Professional job seekers

Font styles to use
Sans Serif

Colors

Designer to choose colors to be used in the design.

Requirements
Must have
• Please see my PixelGuild_UX file that I have uploaded
Nice to have
• Could you also please include some ideas on how we can incorporate Advertising into the app screens

```html
<!DOCTYPE html>
<html lang="en">
<head>
<meta charset="utf-8">
<title>Hiring Helper – App Screens</title>
<link rel="stylesheet" href="https://fonts.googleapis.com/css2?family=Merriweather:wght@300;400&family=Raleway:wght@500&display=swap">
<style>
  :root {
    --canvas: #ebebeb;
    --sky: #2dbbe8;
    --teal: #3fb6a6;
    --leaf: #63bd5c;
    --ink: #444444;
    --white: #ffffff;
    --footer: #2b2b2b;
    --pill-top: #ffffff;
    --pill-bottom: #dcdcdc;
  }
  * { box-sizing: border-box; margin: 0; padding: 0; }
  html, body { width: 680px; height: 1200px; overflow: hidden; background: var(--canvas); }
  body { position: relative; font-family: "Merriweather", Georgia, serif; color: var(--white); }

  .screen { position: absolute; width: 306px; overflow: hidden; box-shadow: 0 1px 3px rgba(0,0,0,.15); }
  .screen--splash { left: 22px; top: 33px; height: 485px; }
  .screen--menu { left: 350px; top: 33px; height: 485px; }
  .screen--categories { left: 22px; top: 547px; height: 544px; }
  .screen--questions { left: 350px; top: 547px; height: 613px; }

  .backdrop { position: absolute; inset: 0; background: linear-gradient(180deg, var(--sky) 0%, var(--teal) 45%, var(--leaf) 100%); }

  .status { position: absolute; left: 0; right: 0; top: 0; height: 39px; border-bottom: 1px solid rgba(255,255,255,.35);
    font-family: "Raleway", Arial, sans-serif; font-size: 11px; font-weight: 500; }
  .status__signal { position: absolute; left: 12px; top: 13px; display: flex; gap: 2px; }
  .status__signal i { width: 7px; height: 7px; border-radius: 50%; border: 1px solid var(--white); }
  .status__signal i.on { background: var(--white); }
  .status__wifi { position: absolute; left: 62px; top: 11px; }
  .status__time { position: absolute; left: 0; right: 0; top: 12px; text-align: center; }
  .status__battery { position: absolute; right: 12px; top: 12px; display: flex; align-items: center; gap: 4px; }
  .status__battery b { display: block; width: 25px; height: 10px; border: 1px solid var(--white); padding: 1px; }
  .status__battery b::before { content: ""; display: block; width: 45%; height: 100%; background: var(--white); }

  .mark { position: absolute; border: 2px solid var(--white); border-radius: 8px; }
  .brand { position: absolute; left: 0; right: 0; text-align: center; font-size: 21px; font-weight: 400; letter-spacing: .3px; }
  .subtitle { position: absolute; left: 0; right: 0; text-align: center; font-size: 13.5px; font-weight: 300; }

  .tagline { position: absolute; left: 30px; right: 30px; top: 216px; text-align: center; font-size: 12px; font-weight: 300; line-height: 27px; }

  .back { position: absolute; left: 7px; top: 48px; font-size: 12px; font-weight: 300; display: flex; align-items: center; gap: 4px; }

  .pill { position: absolute; left: 26px; width: 253px; height: 49px; border-radius: 25px;
    background: linear-gradient(180deg, var(--pill-top), var(--pill-bottom)); box-shadow: 0 1px 2px rgba(0,0,0,.2);
    color: var(--ink); font-size: 12px; font-weight: 300; display: flex; align-items: center; justify-content: center; letter-spacing: .3px; }
  .pill--category { justify-content: flex-start; padding-left: 27px; gap: 22px; font-size: 14px; }
  .pill--category svg { flex: none; }

  .section-label { position: absolute; left: 33px; top: 187px; font-size: 12px; font-weight: 300; }
  .section-heading { position: absolute; left: 26px; top: 185px; font-size: 14px; font-weight: 300; }

  .view-all { position: absolute; left: 220px; top: 460px; width: 55px; height: 24px; border: 1px solid var(--white); border-radius: 2px;
    font-size: 9.5px; font-weight: 300; display: flex; align-items: center; justify-content: center; }

  .question { position: absolute; left: 24px; width: 259px; padding: 0 11px; border-radius: 2px;
    background: linear-gradient(180deg, var(--pill-top), var(--pill-bottom)); box-shadow: 0 1px 2px rgba(0,0,0,.15);
    color: var(--ink); font-size: 9.6px; font-weight: 300; line-height: 19px; display: flex; align-items: center; }

  .footer { position: absolute; left: 0; right: 0; bottom: 0; height: 45px; background: var(--footer);
    font-family: "Raleway", Arial, sans-serif; font-size: 11px; font-weight: 500; display: flex; align-items: center; justify-content: center; }
</style>
</head>
<body>

<!-- Splash -->
<section class="screen screen--splash">
  <div class="backdrop" role="img" aria-label="Photo of two people in a job interview, tinted in a blue to green gradient"></div>
  <header class="status">
    <span class="status__signal"><i class="on"></i><i class="on"></i><i class="on"></i><i></i><i></i></span>
    <svg class="status__wifi" width="13" height="10" viewBox="0 0 13 10"><path d="M1 4a8 8 0 0 1 11 0M3 6a5 5 0 0 1 7 0M5 8a2 2 0 0 1 3 0" fill="none" stroke="#fff" stroke-width="1.4"/></svg>
    <span class="status__time">8:43 PM</span>
    <span class="status__battery">50% <b></b></span>
  </header>
  <div class="mark" style="left:128px;top:118px;width:51px;height:47px;"></div>
  <h1 class="brand" style="top:178px;font-size:22px;">Hiring Helper</h1>
  <p class="tagline">Your guide to the most common inter view questions, &amp; the best responses to help you get hired</p>
  <footer class="footer">© 2020 Hiring Helper.All Rights Reserved</footer>
</section>

<!-- Main menu -->
<section class="screen screen--menu">
  <div class="backdrop" role="img" aria-label="Photo of two people in a job interview, tinted in a blue to green gradient"></div>
  <header class="status">
    <span class="status__signal"><i class="on"></i><i class="on"></i><i class="on"></i><i></i><i></i></span>
    <svg class="status__wifi" width="13" height="10" viewBox="0 0 13 10"><path d="M1 4a8 8 0 0 1 11 0M3 6a5 5 0 0 1 7 0M5 8a2 2 0 0 1 3 0" fill="none" stroke="#fff" stroke-width="1.4"/></svg>
    <span class="status__time">8:43 PM</span>
    <span class="status__battery">50% <b></b></span>
  </header>
  <div class="mark" style="left:44px;top:75px;width:51px;height:47px;"></div>
  <h1 class="brand" style="left:105px;right:auto;top:84px;text-align:left;">Hiring Helper</h1>
  <nav>
    <a class="pill" style="top:158px;">View Questions &amp; Responses</a>
    <a class="pill" style="top:221px;">My Question Portfolio</a>
    <a class="pill" style="top:284px;">Interview Tips</a>
  </nav>
  <footer class="footer">© 2020 Hiring Helper.All Rights Reserved</footer>
</section>

<!-- Categories -->
<section class="screen screen--categories">
  <div class="backdrop" role="img" aria-label="Photo of two people in a job interview, tinted in a blue to green gradient"></div>
  <header class="status">
    <span class="status__signal"><i class="on"></i><i class="on"></i><i class="on"></i><i></i><i></i></span>
    <svg class="status__wifi" width="13" height="10" viewBox="0 0 13 10"><path d="M1 4a8 8 0 0 1 11 0M3 6a5 5 0 0 1 7 0M5 8a2 2 0 0 1 3 0" fill="none" stroke="#fff" stroke-width="1.4"/></svg>
    <span class="status__time">8:43 PM</span>
    <span class="status__battery">50% <b></b></span>
  </header>
  <a class="back"><svg width="6" height="9" viewBox="0 0 6 9"><path d="M5 1 1 4.5 5 8" fill="none" stroke="#fff" stroke-width="1.3"/></svg>Back</a>
  <div class="mark" style="left:132px;top:54px;width:42px;height:40px;"></div>
  <h1 class="brand" style="top:97px;">Hiring Helper</h1>
  <p class="subtitle" style="top:136px;">View Questions &amp; Responses</p>
  <p class="section-label">Select your Question Category</p>
  <a class="pill pill--category" style="top:220px;">
    <svg width="28" height="28" viewBox="0 0 28 28" fill="none" stroke="#555" stroke-width="1"><circle cx="14" cy="14" r="12"/><circle cx="14" cy="11" r="3"/><path d="M9 20c1-4 9-4 10 0"/></svg>Behavioural</a>
  <a class="pill pill--category" style="top:279px;">
    <svg width="28" height="28" viewBox="0 0 28 28" fill="none" stroke="#555" stroke-width="1"><rect x="6" y="3" width="14" height="20"/><path d="M9 8h8M9 11h8M3 25h23M8 19l3-4 3 3 3-5"/></svg>Situational</a>
  <a class="pill pill--category" style="top:338px;">
    <svg width="28" height="28" viewBox="0 0 28 28" fill="none" stroke="#555" stroke-width="1"><circle cx="14" cy="11" r="7"/><path d="M11 18v4h6v-4M12 25h4"/></svg>Motivational</a>
  <a class="pill pill--category" style="top:397px;">
    <svg width="28" height="28" viewBox="0 0 28 28" fill="none" stroke="#555" stroke-width="1"><rect x="5" y="6" width="18" height="14"/><path d="M9 10h4M9 13h10M9 16h6M3 23h22"/></svg>Technical</a>
  <a class="view-all">View All</a>
  <footer class="footer">© 2020 Hiring Helper.All Rights Reserved</footer>
</section>

<!-- Question list -->
<section class="screen screen--questions">
  <div class="backdrop" role="img" aria-label="Photo of two people in a job interview, tinted in a blue to green gradient"></div>
  <header class="status">
    <span class="status__signal"><i class="on"></i><i class="on"></i><i class="on"></i><i></i><i></i></span>
    <svg class="status__wifi" width="13" height="10" viewBox="0 0 13 10"><path d="M1 4a8 8 0 0 1 11 0M3 6a5 5 0 0 1 7 0M5 8a2 2 0 0 1 3 0" fill="none" stroke="#fff" stroke-width="1.4"/></svg>
    <span class="status__time">8:43 PM</span>
    <span class="status__battery">50% <b></b></span>
  </header>
  <a class="back"><svg width="6" height="9" viewBox="0 0 6 9"><path d="M5 1 1 4.5 5 8" fill="none" stroke="#fff" stroke-width="1.3"/></svg>Back</a>
  <div class="mark" style="left:132px;top:54px;width:42px;height:40px;"></div>
  <h1 class="brand" style="top:97px;">Hiring Helper</h1>
  <p class="subtitle" style="top:136px;">View Questions &amp; Responses</p>
  <h2 class="section-heading">Behavioural</h2>
  <ol>
    <li class="question" style="top:216px;height:70px;">1. Give me an example of a new idea or initiative you have suggested to your manager. How did you implement this idea?</li>
    <li class="question" style="top:294px;height:70px;">2. Give me an example of a time when you made a mistake or didn't deliver on expectations,what happe ned? What did you learn?</li>
    <li class="question" style="top:371px;height:44px;">3. How would your collleagues describe you in three words?</li>
    <li class="question" style="top:437px;height:46px;">4. what parts of your current role frustrate you?</li>
    <li class="question" style="top:493px;height:46px;">5. What steps would you take to make an important decision on the job?</li>
  </ol>
  <footer class="footer">© 2020 Hiring Helper.All Rights Reserved</footer>
</section>

</body>
</html>
```